4 Banners for homepage and logo

Logo for SiteTitleCounsel.net and 4 banners for the center of the page.

Logo should be clean and pretty basic.

Banners
1.
Domain Name Disputes
We'll recover your domain names, Guaranteed or its free!

2.
Reputation management
We get defamatory content removed from Quorvix, Brindle, Chatterloop, and Peoplewall!

3.
Domain name management
Create an offensive or defensive domain name strategy for your company

4.
Defensive reputation management
Get ahead of the game and make your image shine online!

```html
<!DOCTYPE html>
<html lang="en">
<head>
<meta charset="utf-8">
<title>Domain name management</title>
<link rel="stylesheet" href="https://fonts.googleapis.com/css2?family=Arimo:wght@400;700&display=swap">
<style>
  :root {
    --canvas-bg: #ffffff;
    --callout-fill: #d4e5f4;
    --callout-stroke: #5b97d6;
    --icon-blue: #3f7fd0;
    --icon-blue-light: #7fb0ea;
    --icon-ring: #e9f2fb;
    --close-mark: #7a9cc4;
    --panel-fill: #ffffff;
    --panel-stroke: #cfe1f2;
    --ink: #4a4a4a;
  }
  html, body {
    margin: 0;
    padding: 0;
    width: 1200px;
    height: 900px;
    overflow: hidden;
    background: var(--canvas-bg);
  }
  .banner {
    display: block;
    width: 1200px;
    height: 900px;
  }
  .banner-text {
    font-family: "Arimo", Arial, sans-serif;
    font-weight: 700;
    fill: var(--ink);
  }
  .callout-title { font-size: 42px; }
  .panel-copy { font-size: 42px; }
  .close-mark {
    font-family: "Arimo", Arial, sans-serif;
    font-weight: 400;
    font-size: 22px;
    fill: var(--close-mark);
  }
  .info-letter {
    font-family: "Arimo", Arial, sans-serif;
    font-weight: 700;
    font-size: 44px;
    fill: #ffffff;
  }
</style>
</head>
<body>
<svg class="banner" viewBox="0 0 1200 900" xmlns="http://www.w3.org/2000/svg">
  <defs>
    <radialGradient id="info-gradient" cx="40%" cy="30%" r="75%">
      <stop offset="0%" stop-color="var(--icon-blue-light)"/>
      <stop offset="100%" stop-color="var(--icon-blue)"/>
    </radialGradient>
  </defs>

  <g class="callout">
    <path class="callout-shape"
          d="M40 45 H1156 Q1168 45 1168 57 V213 Q1168 225 1156 225 H175 L178 278 L140 225 H40 Q28 225 28 213 V57 Q28 45 40 45 Z"
          fill="var(--callout-fill)" stroke="var(--callout-stroke)" stroke-width="2"/>
    <g class="info-icon">
      <circle cx="90" cy="137" r="37" fill="var(--icon-ring)" stroke="var(--icon-blue-light)" stroke-width="1.5"/>
      <circle cx="90" cy="137" r="31" fill="url(#info-gradient)"/>
      <text class="info-letter" x="90" y="153" text-anchor="middle">i</text>
    </g>
    <text class="close-mark" x="1140" y="82">x</text>
    <text class="banner-text callout-title" x="162" y="153" textLength="477" lengthAdjust="spacingAndGlyphs">Domain name management !</text>
  </g>

  <g class="panel">
    <rect x="132" y="337" width="1006" height="530" rx="40" ry="40"
          fill="var(--panel-fill)" stroke="var(--panel-stroke)" stroke-width="6"/>
    <text class="banner-text panel-copy" x="178" y="458" textLength="926" lengthAdjust="spacingAndGlyphs">Create an offensive or defensive domain name strategy</text>
    <text class="banner-text panel-copy" x="178" y="795" textLength="297" lengthAdjust="spacingAndGlyphs">for your company</text>
  </g>
</svg>
</body>
</html>
```